Landingpage design

We need a landingpage for a Chatterloom add campaign. We sell socks made of bamboo in super quality. Our customers loves us, and we have a 5 heart rating at scorevane.com.

We want to create a add campaign targeted new customers, and the offer is that they can buy 1 pair of bamboo socks as a test, for only 20 DKK (2,7 Euro) including shipment. Our webpage is www.tuvelo.dk, landingpage should be built i Kyvio, a wysiwyg editor. based on their template. like:
https://tuvelo.pemlorsite.com/13844-sales-page
https://tuvelo.pemlorsite.com/13696-sales-page
https://tuvelo.pemlorsite.com/13845-sales-page

You don't have to follow the templates 100% if you have better ideas. We have an account for snapvaultly, so please get stockphotos from here.

Bamboo socks has a lot of great selling points, you can see a good desciption here:
https://feltrano.com/us/why-bamboo

We expect you to have experience in landingpage design, and expect to end up with 2 landingpages we can splittest on.

This is the first of a number of landingpages we need in the future, so for the right person there will be plenty of more work.

Target Market(s)

Denmark

Industry/Entity Type

E-Commerce

Number of Pages Required

2 page

Colors

Designer to choose colors to be used in the design.

Requirements
Must have
• A great selling page, showing all the great things with bamboo socks. It should be supplied with good packshots from snapvaultly.com

```html
<!DOCTYPE html>
<html lang="en">
<head>
<meta charset="utf-8">
<title>Tuvelo – Bamboo Socks</title>
<link href="https://fonts.googleapis.com/css2?family=Roboto:wght@300;400;500;700&display=swap" rel="stylesheet">
<style>
:root{
  --green:#3fb38a;
  --ink:#2b2f3a;
  --text:#6d717a;
  --muted:#9a9ea6;
  --light:#f2f3f4;
  --navy:#1e2233;
  --white:#ffffff;
  --blue-top:#7fd6ee;
  --blue-bottom:#4a8fe6;
  --star:#f4b400;
  --leaf-soft:#e3ece0;
}
*{box-sizing:border-box;margin:0;padding:0}
html,body{width:1200px;height:5099px;overflow:hidden}
body{font-family:"Roboto",Arial,sans-serif;color:var(--ink);background:var(--white);position:relative}
.wrap{width:1000px;margin:0 auto;position:relative}
.btn{display:inline-block;background:var(--green);color:#fff;font-size:13px;font-weight:500;text-transform:uppercase;letter-spacing:.5px;padding:11px 0;width:196px;text-align:center;border-radius:2px}
.btn-outline{display:inline-flex;align-items:center;justify-content:center;gap:8px;border:1px solid #fff;color:#fff;font-size:13px;font-weight:500;text-transform:uppercase;width:196px;padding:10px 0;border-radius:2px}
.photo{position:absolute}
h2.section-title{font-size:34px;font-weight:500;text-align:center;color:var(--ink)}
.lead{font-size:15px;line-height:1.7;color:var(--text);text-align:center}

/* header */
.site-header{height:68px;display:flex;align-items:center}
.site-header .wrap{display:flex;align-items:center;justify-content:space-between}
.brand{display:flex;align-items:center;gap:10px}
.brand-mark{width:38px;height:38px;background:var(--ink)}
.brand-name{font-size:14px;font-weight:500;line-height:1.25;color:var(--ink)}
.brand-name small{display:block;font-weight:400;font-size:11px;color:var(--text)}
.nav{display:flex;align-items:center;gap:40px;font-size:12px;text-transform:uppercase;color:var(--text)}
.nav .active{color:var(--ink);border-bottom:2px solid var(--green);padding-bottom:4px}
.nav .btn{width:160px;padding:9px 0;font-size:12px}

/* hero */
.hero{position:relative;height:494px;background:linear-gradient(90deg,#3a3a3a 0%,#4d4c4a 45%,#6f6c68 100%);color:#fff;overflow:hidden}
.hero .wrap{padding-top:95px}
.hero h1{font-size:42px;font-weight:500;line-height:1.2;width:640px}
.checks{list-style:none;margin-top:20px}
.checks li{display:flex;align-items:center;gap:10px;font-size:15px;line-height:1.75}
.checks svg{flex:none}
.hero-actions{margin-top:28px;display:flex;gap:16px}
.note{font-size:11px;margin-top:8px;opacity:.85}

/* why */
.why{background:var(--light);height:588px;padding-top:100px}
.why .lead{width:620px;margin:24px auto 0}
.cards{display:flex;gap:16px;margin-top:50px;justify-content:center}
.card{width:218px;height:194px;background:#fff;text-align:center;padding:28px 22px 0}
.card h3{font-size:16px;font-weight:400;margin:14px 0 8px}
.card p{font-size:11px;line-height:1.6;color:var(--muted)}

/* features */
.feature{position:relative;height:327px;background:#fff;overflow:hidden}
.feature .text{position:absolute;top:90px;width:440px}
.feature h3{font-size:26px;font-weight:500;margin-bottom:18px}
.feature p{font-size:14.5px;line-height:1.75;color:var(--text)}

/* discount */
.discount{height:208px;background:linear-gradient(90deg,#e6f2ea,#dbeee3 60%,#e8f3ec);display:flex;align-items:center}
.discount .wrap{display:flex;align-items:center}
.discount .big{font-size:78px;font-weight:700;color:var(--green);letter-spacing:-1px}
.discount h3{font-size:23px;font-weight:500;margin-left:30px;width:420px;line-height:1.3}
.discount .cta{margin-left:auto;text-align:center}
.discount .note{color:var(--muted)}

/* facts */
.facts{height:561px;background:linear-gradient(180deg,var(--blue-top),var(--blue-bottom));color:#fff;padding-top:95px;text-align:center}
.facts h2{font-size:32px;font-weight:500}
.facts .lead{color:#fff;width:600px;margin:20px auto 0;font-weight:500}
.fact-row{display:flex;justify-content:center;gap:40px;margin-top:60px}
.fact{width:290px}
.fact .icon{width:80px;height:80px;border-radius:50%;background:rgba(255,255,255,.25);display:flex;align-items:center;justify-content:center;margin:0 auto 22px}
.fact .icon span{width:48px;height:48px;border-radius:50%;background:#fff;display:flex;align-items:center;justify-content:center}
.fact p{font-size:14px;line-height:1.7}

/* video */
.video{height:721px;position:relative;padding-top:100px;background:#fff;overflow:hidden}
.video .lead{width:620px;margin:20px auto 0}
.video-frame{width:620px;height:342px;margin:40px auto 0;position:relative;background:linear-gradient(135deg,#5a3b26,#8a5c3b 50%,#4b3224)}
.play{position:absolute;left:50%;top:50%;width:58px;height:58px;margin:-29px 0 0 -29px;border-radius:50%;background:var(--green);display:flex;align-items:center;justify-content:center}
.foliage{position:absolute;background:var(--leaf-soft)}

/* rating */
.rating{height:795px;padding-top:100px;background:#fff;text-align:center}
.stars{display:flex;justify-content:center}
.rating .lead{width:420px;margin:16px auto 0}
.reviews{position:relative;display:flex;justify-content:center;gap:28px;margin-top:56px}
.review{width:296px;height:318px;background:var(--light);text-align:left;padding:28px 28px 0}
.reviewer{display:flex;align-items:center;gap:12px}
.avatar{width:44px;height:44px;border-radius:50%;background:#c9cdd2}
.reviewer b{display:block;font-size:14px;font-weight:500}
.review p{font-size:13px;line-height:1.7;color:var(--text);margin-top:30px}
.arrow{position:absolute;top:140px}
.rating .btn{margin-top:42px;width:228px}

/* final */
.final{position:relative;height:442px;background:linear-gradient(90deg,#eeeeee,#f4f4f4)}
.final .wrap{padding-top:80px}
.final h2{font-size:40px;font-weight:500;line-height:1.2;width:600px}
.final .checks li{color:var(--text);font-size:14px}
.final .btn{margin-top:26px}
.final .note{color:var(--muted)}

/* footer */
.site-footer{height:241px;background:var(--navy);color:#fff;padding-top:58px}
.site-footer .wrap{display:flex;gap:40px}
.fcol{width:300px;font-size:12px;line-height:1.65;color:#c8cbd3}
.fcol h4{font-size:18px;font-weight:500;color:#fff;margin-bottom:14px}
.social{width:22px;height:22px;border-radius:50%;background:#fff;margin-top:10px}
</style>
</head>
<body>

<header class="site-header">
  <div class="wrap">
    <div class="brand">
      <span class="brand-mark"></span>
      <span class="brand-name">Tuvelo i bambus -<small>bløde og enkle</small></span>
    </div>
    <nav class="nav">
      <span class="active">Home</span><span>Why Bamboo</span><span>About us</span><span>Reviews</span>
      <span class="btn">Buy now</span>
    </nav>
  </div>
</header>

<section class="hero">
  <div class="photo" role="img" aria-label="Photo of feet in dark bamboo socks resting on a sofa" style="left:560px;top:0;width:640px;height:494px;background:linear-gradient(90deg,rgba(0,0,0,0),#1e1e1e 60%,#2a2a2a)"></div>
  <div class="wrap">
    <h1>Enjoy Your First Pair of Bamboo Socks for Only 20 DKK</h1>
    <ul class="checks">
      <li><svg width="14" height="14" viewBox="0 0 14 14"><path d="M2 7l3 3 7-7" stroke="#3fb38a" stroke-width="2" fill="none"/></svg>We have been working on textile for more than 10 years</li>
      <li><svg width="14" height="14" viewBox="0 0 14 14"><path d="M2 7l3 3 7-7" stroke="#3fb38a" stroke-width="2" fill="none"/></svg>All products meet our high quality standards</li>
      <li><svg width="14" height="14" viewBox="0 0 14 14"><path d="M2 7l3 3 7-7" stroke="#3fb38a" stroke-width="2" fill="none"/></svg>Our customers loves us, and we have a 5 stars rating at scorevane.com</li>
    </ul>
    <div class="hero-actions">
      <span class="btn">Buy now</span>
      <span class="btn-outline"><svg width="10" height="12" viewBox="0 0 10 12"><path d="M0 0l10 6-10 6z" fill="#fff"/></svg>Watch video</span>
    </div>
    <p class="note">Shipment included</p>
  </div>
</section>

<section class="why">
  <h2 class="section-title">Why Bamboo Clothing?</h2>
  <p class="lead">It was only in 2011 that the Hollin University discovered how you can make fabric from bamboo stems. Now bamboo has the potential to become the textile of the future.</p>
  <div class="cards">
    <div class="card">
      <svg width="34" height="30" viewBox="0 0 34 30"><path d="M11 2l-9 5 3 7 4-2v16h16V12l4 2 3-7-9-5c-1 3-3 5-6 5s-5-2-6-5z" fill="none" stroke="#3fb38a" stroke-width="2"/></svg>
      <h3>Comfortable</h3><p>Bamboo fabric breathes, making you comfortable in garments made in this.</p>
    </div>
    <div class="card">
      <svg width="32" height="32" viewBox="0 0 32 32"><path d="M6 26C6 12 14 5 28 4c0 14-7 22-22 22zM6 26l12-12" fill="none" stroke="#3fb38a" stroke-width="2"/></svg>
      <h3>Eco-friendly</h3><p>Bamboo is a very fast growing, tropical forest product, which does not require the use of pesticides.</p>
    </div>
    <div class="card">
      <svg width="32" height="32" viewBox="0 0 32 32"><path d="M16 3l12 7v12l-12 7-12-7V10zM4 10l12 7 12-7M16 17v12" fill="none" stroke="#3fb38a" stroke-width="2"/></svg>
      <h3>Exquisitely soft</h3><p>The moment you wear it next to your skin you will notice the difference between other fabrics.</p>
    </div>
    <div class="card">
      <svg width="30" height="32" viewBox="0 0 30 32"><path d="M11 3h8M12 3v10L3 28h24L18 13V3M8 21h14" fill="none" stroke="#3fb38a" stroke-width="2"/></svg>
      <h3>Thermo-control</h3><p>Bamboo fabric is warm, thanks to its hollow microfibre, yet is also breathable.</p>
    </div>
  </div>
</section>

<section class="feature">
  <div class="photo" role="img" aria-label="Photo of black bamboo socks beside leather shoes" style="left:0;top:0;width:600px;height:327px;background:linear-gradient(135deg,#2c2c2c,#6c6c6c 55%,#9a9a9a)"></div>
  <div class="text" style="left:648px">
    <h3>Strong Material</h3>
    <p>Bamboo fabric is lightweight yet strong. The natural processing of linen bamboo allows the fibre to remain strong to produce an extremely high quality product. This process gives a material that is very durable.</p>
  </div>
</section>

<section class="feature">
  <div class="text" style="left:133px">
    <h3>Completely Clean</h3>
    <p>Bamboo fibers doesnt under go much chemical processing to make the fabric, so you can easily wear it without causing any allergic irritation to the skin that is more prevalent with heavily processed fabrics.</p>
  </div>
  <div class="photo" role="img" aria-label="Photo of a family relaxing on a sofa wearing bamboo socks" style="left:600px;top:0;width:600px;height:327px;background:linear-gradient(135deg,#d8cdbf,#b7a48e 50%,#8b7460)"></div>
</section>

<section class="feature">
  <div class="photo" role="img" aria-label="Photo of feet in wool socks warming by a fireplace" style="left:0;top:0;width:600px;height:327px;background:linear-gradient(135deg,#2a1a12,#8a3a12 50%,#d86a1c 75%,#3a241a)"></div>
  <div class="text" style="left:648px">
    <h3>Water Absorbent</h3>
    <p>Bamboo fibers are water absorbent. So if you live in a humid environment this is the fabric for you. Think of the sweat it will absorb and evaporate out of your body.</p>
  </div>
</section>

<section class="discount">
  <div class="wrap">
    <span class="big">-90%</span>
    <h3>Get Your First Pair of Socks With an Exclusive Discount</h3>
    <div class="cta"><span class="btn">Buy now</span><p class="note">Shipment included</p></div>
  </div>
</section>

<section class="facts">
  <h2>A Few Facts About Tuvelo</h2>
  <p class="lead">We have been working on textile for more than 10 years. This ensures that all products meet our high quality standards.</p>
  <div class="fact-row">
    <div class="fact">
      <div class="icon"><span><svg width="22" height="20" viewBox="0 0 22 20"><path d="M7 1L1 4l2 5 3-2v12h10V7l3 2 2-5-6-3c-1 2-2 3-4 3S8 3 7 1z" fill="#4a8fe6"/></svg></span></div>
      <p>Our mission is to give our customers access to quality products at a reasonable price.</p>
    </div>
    <div class="fact">
      <div class="icon"><span><svg width="20" height="22" viewBox="0 0 20 22"><path d="M3 1h14v20H3z" fill="none" stroke="#4a8fe6" stroke-width="2"/><path d="M6 7h8M6 11h8M6 15h5" stroke="#4a8fe6" stroke-width="2"/></svg></span></div>
      <p>We know that the properties of bamboo are absolutely amazing and can reduce, for example, sweaty and sour toes.</p>
    </div>
    <div class="fact">
      <div class="icon"><span><svg width="22" height="22" viewBox="0 0 22 22"><circle cx="11" cy="9" r="7" fill="none" stroke="#4a8fe6" stroke-width="2"/><path d="M7 15l-2 6 6-3 6 3-2-6" fill="none" stroke="#4a8fe6" stroke-width="2"/></svg></span></div>
      <p>We shop directly with the factories. This ensures the highest quality at a competitive price.</p>
    </div>
  </div>
</section>

<section class="video">
  <div class="foliage" role="img" aria-label="Decorative bamboo leaves in the corner" style="left:0;top:0;width:170px;height:150px"></div>
  <div class="foliage" role="img" aria-label="Decorative bamboo leaves along the edge" style="right:0;top:430px;width:150px;height:291px"></div>
  <h2 class="section-title">A Short Video About Our Work</h2>
  <p class="lead">We sell stockings, t-shirts, sweaters and men's boxershorts. If you choose our subscription service, the products will come to you automatically.</p>
  <div class="video-frame" role="img" aria-label="Video still of neatly packed clothes and accessories on a wooden floor">
    <span class="play"><svg width="18" height="20" viewBox="0 0 18 20"><path d="M0 0l18 10L0 20z" fill="#fff"/></svg></span>
  </div>
</section>

<section class="rating">
  <div class="stars">
    <svg width="150" height="28" viewBox="0 0 150 28"><g fill="#f4b400"><path id="s" d="M14 1l4 8.5 9 1-6.7 6.2 1.8 9L14 21l-8.1 4.7 1.8-9L1 10.5l9-1z"/><use href="#s" x="30"/><use href="#s" x="60"/><use href="#s" x="90"/><use href="#s" x="120"/></g></svg>
  </div>
  <h2 class="section-title" style="margin-top:10px">We Have a 5 Stars Rating</h2>
  <p class="lead">You're in a good company. Here are some important facts and testimonials about us.</p>
  <div class="reviews">
    <svg class="arrow" style="left:0" width="12" height="18" viewBox="0 0 12 18"><path d="M10 2L3 9l7 7" stroke="#3fb38a" stroke-width="2.5" fill="none"/></svg>
    <div class="review">
      <div class="reviewer"><span class="avatar"></span><div><b>Tom Harlow</b><svg width="70" height="12" viewBox="0 0 150 28"><g fill="#f4b400"><use href="#s"/><use href="#s" x="30"/><use href="#s" x="60"/><use href="#s" x="90"/><use href="#s" x="120"/></g></svg></div></div>
      <p>Lorem ipsum dolor sit amet, consetetur sadipscing elitr, sed diam nonumy eirmod tempor invidunt ut labore et dolore magna aliquyam erat, sed diam voluptua. At vero eos et accusam et justo duo.</p>
    </div>
    <div class="review">
      <div class="reviewer"><span class="avatar"></span><div><b>Tom Harlow</b><svg width="70" height="12" viewBox="0 0 150 28"><g fill="#f4b400"><use href="#s"/><use href="#s" x="30"/><use href="#s" x="60"/><use href="#s" x="90"/><use href="#s" x="120"/></g></svg></div></div>
      <p>Lorem ipsum dolor sit amet, consetetur sadipscing elitr, sed diam nonumy eirmod tempor invidunt ut labore et dolore magna aliquyam erat, sed diam voluptua. At vero eos et accusam et justo duo.</p>
    </div>
    <div class="review">
      <div class="reviewer"><span class="avatar"></span><div><b>Tom Harlow</b><svg width="70" height="12" viewBox="0 0 150 28"><g fill="#f4b400"><use href="#s"/><use href="#s" x="30"/><use href="#s" x="60"/><use href="#s" x="90"/><use href="#s" x="120"/></g></svg></div></div>
      <p>Lorem ipsum dolor sit amet, consetetur sadipscing elitr, sed diam nonumy eirmod tempor invidunt ut labore et dolore magna aliquyam erat, sed diam voluptua. At vero eos et accusam et justo duo.</p>
    </div>
    <svg class="arrow" style="right:0" width="12" height="18" viewBox="0 0 12 18"><path d="M2 2l7 7-7 7" stroke="#3fb38a" stroke-width="2.5" fill="none"/></svg>
  </div>
  <span class="btn">More reviews</span>
</section>

<section class="final">
  <div class="photo" role="img" aria-label="Photo of a smiling woman in a knit hat and pink sweater holding a paper shopping bag" style="left:760px;top:0;width:440px;height:442px;background:linear-gradient(180deg,#f1f1f1,#e9c7c6 45%,#e28a86 75%,#c69a6e)"></div>
  <div class="wrap">
    <h2>Get Your First Pair of Bamboo Socks for Only 20 DKK</h2>
    <ul class="checks">
      <li><svg width="14" height="14" viewBox="0 0 14 14"><path d="M2 7l3 3 7-7" stroke="#3fb38a" stroke-width="2" fill="none"/></svg>Powerfully insulating - keeps you cooler in summer and warmer in winter</li>
      <li><svg width="14" height="14" viewBox="0 0 14 14"><path d="M2 7l3 3 7-7" stroke="#3fb38a" stroke-width="2" fill="none"/></svg>Antibacterial - keeps you odour free and feeling and smelling fresh</li>
      <li><svg width="14" height="14" viewBox="0 0 14 14"><path d="M2 7l3 3 7-7" stroke="#3fb38a" stroke-width="2" fill="none"/></svg>Most eco-friendly fabric on the planet - help save your planet</li>
    </ul>
    <span class="btn">Buy now</span>
    <p class="note">Shipment included</p>
  </div>
</section>

<footer class="site-footer">
  <div class="wrap">
    <div class="fcol">
      <h4>About us</h4>
      <p>At Tuvelo.dk we specialize in basic products in bamboo. We sell stockings, t-shirts, sweaters and men's boxershorts.</p>
      <div class="social" aria-label="Chatterloom"></div>
    </div>
    <div class="fcol">
      <h4>Contact us</h4>
      <p>Any questions? Then e-mail <span style="color:var(--green)">info@tuvelo.dk</span><br>or call us on +45 31 72 40 18</p>
      <p style="margin-top:8px">Or send us a letter to Tuvelo<br>Lindholm 4<br>7100 Vejle</p>
    </div>
    <div class="fcol">
      <h4>Navigation</h4>
      <p>Home &nbsp;|&nbsp; Why Bamboo &nbsp;|&nbsp; About &nbsp;|&nbsp; Reviews</p>
    </div>
  </div>
</footer>

</body>
</html>
```